HearthMile business card and stationary design

We are looking for a simple yet elegant design for our mortgage company business card and stationary.

The card should include:
Name (Marcus Pell)
Title (CEO)
Phone Number (732-555-0182)
Address (48 Birchwell Court, Suite 314, Lindenfield, NJ 07999)
Email (email@hearthmile.example)
"NMLS" i.e. (NMLS 61947)
"Company NMLS" (Company NMLS 274615)

Contact Information for Business Card

See above

```html
<!DOCTYPE html>
<html lang="en">
<head>
<meta charset="utf-8">
<title>HearthMile Business Card</title>
<link href="https://fonts.googleapis.com/css2?family=Montserrat:wght@500;600;700&family=Arimo:wght@400&display=swap" rel="stylesheet">
<style>
  :root {
    --stage: #e9ebee;
    --card-white: #ffffff;
    --ink: #18222e;
    --brand-blue: #1aa7e6;
    --rule: #9a9a9a;
    --back-dark: #172330;
    --back-mid: #123a52;
    --back-light: #0a8fc6;
    --white: #ffffff;
  }
  * { box-sizing: border-box; margin: 0; padding: 0; }
  html, body { width: 1200px; height: 1108px; overflow: hidden; }
  body {
    background: var(--stage);
    display: flex;
    align-items: center;
    justify-content: center;
    gap: 100px;
    font-family: "Arimo", Arial, sans-serif;
    color: var(--ink);
  }
  .card {
    width: 400px;
    height: 700px;
    border-radius: 26px;
    overflow: hidden;
    position: relative;
    box-shadow: 0 14px 30px rgba(0,0,0,0.18);
  }
  .card-front {
    background: var(--card-white);
    display: flex;
    flex-direction: column;
    align-items: center;
    text-align: center;
    padding-top: 150px;
  }
  .brand-name {
    font-family: "Montserrat", Arial, sans-serif;
    font-weight: 600;
    font-size: 54px;
    letter-spacing: 0.5px;
    color: var(--ink);
  }
  .person-name {
    margin-top: 60px;
    font-family: "Montserrat", Arial, sans-serif;
    font-weight: 700;
    font-size: 28px;
    line-height: 1;
  }
  .person-name .first { color: var(--ink); }
  .person-name .last { color: var(--brand-blue); }
  .person-title { font-size: 18px; margin-top: 4px; }
  .icon-row {
    display: flex;
    align-items: center;
    width: 300px;
    margin-top: 12px;
    gap: 6px;
  }
  .icon-row .rule { flex: 1; height: 1px; background: var(--rule); }
  .icon-tile {
    width: 36px; height: 36px;
    background: var(--brand-blue);
    border-radius: 5px;
    display: flex; align-items: center; justify-content: center;
  }
  .contact-list { margin-top: 12px; font-size: 18px; line-height: 1.4; }
  .contact-list .accent { color: var(--brand-blue); }
  .divider { width: 300px; height: 1px; background: var(--rule); margin: 14px 0; }
  .address { font-size: 18px; line-height: 1.4; }
  .licence { font-size: 18px; line-height: 1.4; }
  .licence .label { color: var(--brand-blue); }
  .card-back {
    background: linear-gradient(30deg, var(--back-dark) 0%, var(--back-dark) 35%, var(--back-mid) 65%, var(--back-light) 100%);
  }
  .back-pattern-area { position: absolute; inset: 0; }
  .back-brand {
    position: absolute;
    right: 36px;
    bottom: 150px;
    font-family: "Montserrat", Arial, sans-serif;
    font-weight: 600;
    font-size: 42px;
    color: var(--white);
  }
</style>
</head>
<body>
  <section class="card card-front">
    <div class="brand-name">HearthMile</div>
    <div class="person-name"><span class="first">Marcus</span> <span class="last">Pell</span></div>
    <div class="person-title">CEO</div>
    <div class="icon-row">
      <span class="rule"></span>
      <span class="icon-tile" aria-label="Phone">
        <svg width="22" height="22" viewBox="0 0 24 24" fill="none" stroke="#fff" stroke-width="2" stroke-linecap="round" stroke-linejoin="round"><path d="M5 4h4l2 5-2.5 1.5a11 11 0 0 0 5 5L15 13l5 2v4a2 2 0 0 1-2 2A16 16 0 0 1 3 6a2 2 0 0 1 2-2"/></svg>
      </span>
      <span class="icon-tile" aria-label="Email">
        <svg width="22" height="22" viewBox="0 0 24 24" fill="none" stroke="#fff" stroke-width="2" stroke-linejoin="round"><rect x="3" y="6" width="18" height="12"/><path d="M3 6l9 7 9-7"/></svg>
      </span>
      <span class="icon-tile" aria-label="Website">
        <svg width="22" height="22" viewBox="0 0 24 24" fill="none" stroke="#fff" stroke-width="2"><circle cx="12" cy="12" r="9"/><path d="M3 12h18M12 3c3 3 3 15 0 18M12 3c-3 3-3 15 0 18"/></svg>
      </span>
      <span class="rule"></span>
    </div>
    <div class="contact-list">
      <div>732-555-0182</div>
      <div>email@hearthmile.example</div>
      <div>www.<span class="accent">hearthmile</span>.example</div>
    </div>
    <div class="divider"></div>
    <div class="address">
      <div>48 Birchwell Court, Suite 314</div>
      <div>Lindenfield, NJ 07999</div>
    </div>
    <div class="divider"></div>
    <div class="licence">
      <div><span class="label">NMLS</span> 61947</div>
      <div><span class="label">Company NMLS</span> 274615</div>
    </div>
  </section>

  <section class="card card-back">
    <div class="back-pattern-area" role="img" aria-label="Faint repeating brand name pattern over a dark navy to blue gradient"></div>
    <div class="back-brand">HearthMile</div>
  </section>
</body>
</html>
```